Lumra Learning Web Design Project

Who We are:
Lumra Learning is education information portal/ magazine, providing information about the Chinese and International education markets. Our aim is to help school principals improve there curriculum, and parents in understanding this curriculum.

Project Brief:
The site will include education news updates, educational services, curriculum developments and overseas study. We hope the site represents the cross cultural bridge between the west and east. The site will cover both the Sciences and Arts.

Note:
The logo design competition is also underway so we only need the website design

What We want:
This competition is for Design only no coding!
Design a home page based on Template 1,2 or 3. I only need to select one.
The design of an article page.

Optional
Design a Parvex Shutters metro style splash page.

Sites We like:
http://www.qv.com.cn/tonguebridge/default.aspx
http://www.dailyuniversitybulletin.co.uk/
http://kptz.sinocraftlearn.net/

Template Explanations:
Template 1-
The main information has a dynamic sliding category view that when clicked displays the relevant info.
In addition to the main upper menu it also has a left hand sliding menu that pops out on click or gesture

Template 2-
Has limited number of Articles most of the menus are drop downs from the top menu

Template 3-
No Top menu

Target Market(s)

Teachers, principals and parents

Industry/Entity Type

Education

Requirements
Should not have
• kindergarten preschool feel

```html
<!DOCTYPE html>
<html lang="fr">
<head>
<meta charset="utf-8">
<title>Lumra Learning</title>
<link href="https://fonts.googleapis.com/css2?family=Philosopher:wght@400;700&family=Ubuntu:wght@400;500;700&display=swap" rel="stylesheet">
<style>
:root{
  --page:#ebeae6;
  --white:#ffffff;
  --red:#c4161c;
  --blue-title:#1f5fa8;
  --text:#6b6b6b;
  --card:#f4f4f2;
  --meta:#e6e5e1;
  --heading:#7a1f5c;
  --footer:#333333;
  --footer-text:#c9c9c9;
  --nav-home:#d2548b;
  --nav-about:#eeb82e;
  --nav-service:#4caf4a;
  --nav-news:#25a0dc;
  --nav-blog:#9866b8;
  --nav-brand:#7b2a8d;
  --nav-contact:#b3732b;
  --btn-blue:#1d4f86;
  --ad-navy:#0c2a57;
  --ad-sky:#25b3e6;
  --ad-green:#3fb14a;
}
*{box-sizing:border-box;margin:0;padding:0}
html,body{width:1200px;height:2239px;overflow:hidden}
body{background:var(--page);font-family:"Ubuntu",Arial,sans-serif;position:relative;color:var(--text)}
.abs{position:absolute}

/* header */
.site-header{left:100px;top:19px;width:1001px;height:148px;background:var(--white)}
.brand{position:absolute;left:20px;top:48px;display:flex;align-items:center;gap:10px}
.brand-dot{width:40px;height:40px;border-radius:50%;background:var(--red)}
.brand-name{font-weight:700;font-size:22px;color:var(--red);text-transform:uppercase}
.search{position:absolute;left:616px;top:56px;display:flex;gap:6px}
.search-field{width:318px;height:32px;border:1px solid #dcdcdc;border-radius:3px;font-size:11px;font-style:italic;color:#aaa;padding:9px 12px}
.search-btn{width:38px;height:32px;background:var(--red);border-radius:3px;display:flex;align-items:center;justify-content:center}

/* nav */
.side-nav{left:100px;top:178px;width:230px}
.nav-item{height:71px;display:flex;align-items:center;font-family:"Philosopher",sans-serif;font-size:19px;color:#fff;font-weight:700}
.nav-icon{width:62px;height:71px;background:rgba(0,0,0,.12);display:flex;align-items:center;justify-content:center;margin-right:15px}
.social{left:108px;top:696px;display:flex;gap:22px}
.social span{width:24px;height:24px;background:#a3a3a0;border-radius:4px;display:block}

/* main */
.main-panel{left:340px;top:178px;width:761px;height:1717px;background:var(--white)}
.slider{left:351px;top:188px;width:568px;height:300px;background:linear-gradient(100deg,#d9c3b4 0%,#5a6a80 45%,#39434f 100%)}
.slider-title{position:absolute;left:208px;top:26px;width:350px;font-size:29px;font-weight:500;color:#fff;line-height:1.28;white-space:nowrap;text-shadow:0 1px 3px rgba(0,0,0,.5)}
.read-more{position:absolute;left:440px;top:122px;background:var(--red);color:#fff;font-weight:700;font-size:16px;padding:7px 8px;border:1px solid rgba(255,255,255,.2)}

.section-head{position:absolute;left:351px;width:568px;height:32px;display:flex;align-items:center}
.section-head::before{content:"";position:absolute;left:0;right:0;top:9px;height:16px;background:var(--red);border-radius:8px}
.section-head span{position:relative;background:#fff;margin-left:20px;padding:0 12px;font-size:23px;color:var(--heading)}

.card{position:absolute;width:282px;background:var(--card)}
.card-photo{margin:10px 10px 0;height:125px}
.card-title{margin:18px 12px 0;font-size:14.5px;font-weight:500;color:var(--blue-title);text-transform:uppercase;line-height:1.2}
.card-text{margin:8px 14px 0 12px;font-size:12.5px;line-height:1.6}
.card-meta{position:absolute;left:0;right:0;bottom:0;height:32px;background:var(--meta);display:flex;align-items:center;gap:16px;padding-left:12px;font-size:12.5px;color:#222}
.card-meta i{display:inline-block;width:11px;height:11px;background:var(--red);margin-right:6px;border-radius:50%;vertical-align:-1px}
.news-date{margin:6px 12px 0;font-size:11px;color:var(--red)}
.news-date i{display:inline-block;width:8px;height:8px;border-radius:50%;background:var(--red);margin-right:5px}
.view-all{position:absolute;left:852px;width:67px;height:26px;border-radius:5px;background:var(--btn-blue);color:#fff;font-size:12.5px;display:flex;align-items:center;justify-content:center}

/* advertising slots */
.ad-slot{position:absolute;left:930px;width:161px}
.ad-slot-top{top:188px;height:600px;background:linear-gradient(var(--ad-navy) 0 78%,#ffffff 78% 89%,#111111 89%)}
.ad-slot-mid{top:797px;height:599px;background:linear-gradient(var(--ad-sky) 0 65%,var(--ad-green) 65%)}
.ad-slot-low{top:1407px;height:438px;background:linear-gradient(#0b60ad 0 10%,var(--ad-navy) 10% 32%,var(--red) 32% 52%,var(--ad-navy) 52%)}

/* footer */
.site-footer{left:100px;top:1916px;width:1001px;height:302px;background:var(--footer)}
.foot-col{position:absolute;top:26px}
.foot-col h4{font-size:15px;font-weight:400;color:#eee;margin-bottom:16px}
.foot-col a{display:block;font-size:11px;color:var(--footer-text);text-decoration:underline;line-height:21px}
.foot-social{display:flex;gap:12px;margin-bottom:26px}
.foot-social span{width:32px;height:32px;background:#1e78b4;border-radius:3px}
.newsletter{display:flex}
.newsletter .field{width:180px;height:30px;background:#222;font-size:10px;font-style:italic;color:#777;padding:9px 10px}
.newsletter .go{width:84px;height:30px;background:var(--red);color:#fff;font-size:12.5px;display:flex;align-items:center;justify-content:center}
.copyright{position:absolute;left:20px;right:20px;top:244px;border-top:1px solid #4a4a4a;padding-top:20px;font-size:11px;color:#999}
</style>
</head>
<body>

<header class="site-header abs">
  <div class="brand"><span class="brand-dot"></span><span class="brand-name">Lumra Learning</span></div>
  <div class="search">
    <div class="search-field">Please enter your search</div>
    <div class="search-btn"><svg width="16" height="16" viewBox="0 0 16 16"><circle cx="6.5" cy="6.5" r="4.5" fill="none" stroke="#fff" stroke-width="2"/><line x1="10" y1="10" x2="14" y2="14" stroke="#fff" stroke-width="2.5"/></svg></div>
  </div>
</header>

<nav class="side-nav abs">
  <div class="nav-item" style="background:var(--nav-home)"><span class="nav-icon"><svg width="34" height="30"><path d="M3 15 17 3l14 12M7 12v15h20V12" fill="none" stroke="#fff" stroke-width="2.5"/></svg></span>Home</div>
  <div class="nav-item" style="background:var(--nav-about)"><span class="nav-icon"><svg width="34" height="30"><ellipse cx="14" cy="12" rx="11" ry="8" fill="#fff"/><ellipse cx="23" cy="19" rx="8" ry="6" fill="#fff"/></svg></span>About Us</div>
  <div class="nav-item" style="background:var(--nav-service)"><span class="nav-icon"><svg width="34" height="30"><path d="M5 5l24 22M29 5 5 27" stroke="#fff" stroke-width="4"/></svg></span>Service</div>
  <div class="nav-item" style="background:var(--nav-news)"><span class="nav-icon"><svg width="34" height="32"><rect x="7" y="2" width="20" height="27" fill="none" stroke="#fff" stroke-width="2.5"/><path d="M11 11h12M11 16h12M11 21h12" stroke="#fff" stroke-width="2"/></svg></span>New &amp; Event</div>
  <div class="nav-item" style="background:var(--nav-blog)"><span class="nav-icon"><svg width="34" height="30"><rect x="3" y="3" width="28" height="24" fill="none" stroke="#fff" stroke-width="2.5"/><path d="M3 9h28M7 14h10v8H7zM20 14h8M20 19h8" stroke="#fff" stroke-width="2"/></svg></span>Blog</div>
  <div class="nav-item" style="background:var(--nav-brand)"><span class="nav-icon"><svg width="34" height="30"><rect x="4" y="3" width="26" height="17" fill="none" stroke="#fff" stroke-width="2.5"/><path d="M17 20v8M10 28h14" stroke="#fff" stroke-width="2.5"/></svg></span>Lumra Learning</div>
  <div class="nav-item" style="background:var(--nav-contact)"><span class="nav-icon"><svg width="34" height="30"><path d="M8 4l6 6-3 4c2 3 4 5 7 7l4-3 6 6-4 4C15 27 7 19 4 8z" fill="#fff"/></svg></span>Contact Us</div>
</nav>
<div class="social abs"><span></span><span></span><span></span><span></span><span></span></div>

<main class="main-panel abs"></main>

<section class="slider abs" role="img" aria-label="Photo of a smiling student holding a red book in a library">
  <div class="slider-title">Contrairement à unei<br>nion répandue</div>
  <div class="read-more">Read More</div>
</section>

<div class="section-head" style="top:503px"><span>Latest Articles</span></div>

<article class="card" style="left:351px;top:540px;height:340px">
  <div class="card-photo" role="img" aria-label="Photo of a student outdoors" style="background:linear-gradient(90deg,#8a5a48,#c9b8a0,#6f8a5c)"></div>
  <h2 class="card-title">Plusieurs variations de Lorem Ipsum peuvent être trouvées ici ou.</h2>
  <p class="card-text">Le Lorem Ipsum est simplement du faux texte employé dans la composition et la mise en page avant impressionLe Lorem Ipsum est le faux texte standard.</p>
  <div class="card-meta"><span><i></i>By Admin</span><span><i></i>June 24, 2013</span></div>
</article>
<article class="card" style="left:642px;top:540px;height:340px">
  <div class="card-photo" role="img" aria-label="Photo of two students studying together" style="background:linear-gradient(90deg,#c2a84a,#e7d9b0,#6b5a3a)"></div>
  <h2 class="card-title">Ensemble des morceaux de texte pour réaliser un livre spécimen de.</h2>
  <p class="card-text">Contrairement à une opinion répandue, le Lorem Ipsum n'est pas simplement du texte aléatoire. Il trouve ses racines dans une oeuvre de la.</p>
  <div class="card-meta"><span><i></i>By Admin</span><span><i></i>June 24, 2013</span></div>
</article>
<article class="card" style="left:351px;top:891px;height:337px">
  <div class="card-photo" role="img" aria-label="Photo of a student outdoors" style="background:linear-gradient(90deg,#8a5a48,#c9b8a0,#6f8a5c)"></div>
  <h2 class="card-title">Plusieurs variations de Lorem Ipsum peuvent être trouvées ici ou.</h2>
  <p class="card-text">Le Lorem Ipsum est simplement du faux texte employé dans la composition et la mise en page avant impressionLe Lorem Ipsum est le faux texte standard.</p>
  <div class="card-meta"><span><i></i>By Admin</span><span><i></i>June 24, 2013</span></div>
</article>
<article class="card" style="left:642px;top:891px;height:337px">
  <div class="card-photo" role="img" aria-label="Photo of two students studying together" style="background:linear-gradient(90deg,#c2a84a,#e7d9b0,#6b5a3a)"></div>
  <h2 class="card-title">Ensemble des morceaux de texte pour réaliser un livre spécimen de.</h2>
  <p class="card-text">Contrairement à une opinion répandue, le Lorem Ipsum n'est pas simplement du texte aléatoire. Il trouve ses racines dans une oeuvre de la.</p>
  <div class="card-meta"><span><i></i>By Admin</span><span><i></i>June 24, 2013</span></div>
</article>
<div class="view-all" style="top:1240px">View All</div>

<div class="section-head" style="top:1280px"><span>Latest News</span></div>

<article class="card" style="left:351px;top:1316px;height:259px">
  <div class="card-photo" role="img" aria-label="Photo of a student reading a book" style="background:linear-gradient(90deg,#7c7a74,#cfc6b6,#4a4a48)"></div>
  <h2 class="card-title">Plusieurs variations de Lorem Ipsum peuvent</h2>
  <div class="news-date"><i></i>June 24, 2013</div>
  <p class="card-text">Le Lorem Ipsum est simplement du faux texte employé dans.</p>
</article>
<article class="card" style="left:642px;top:1316px;height:259px">
  <div class="card-photo" role="img" aria-label="Photo of students chatting" style="background:linear-gradient(90deg,#8a4fa0,#e2cbb6,#dcdcdc)"></div>
  <h2 class="card-title">Plusieurs variations de Lorem Ipsum peuvent</h2>
  <div class="news-date"><i></i>June 24, 2013</div>
  <p class="card-text">Le Lorem Ipsum est simplement du faux texte employé dans.</p>
</article>
<article class="card" style="left:351px;top:1585px;height:258px">
  <div class="card-photo" role="img" aria-label="Photo of a student at a desk with books" style="background:linear-gradient(90deg,#5a4e44,#d8d2c8,#f0efeb)"></div>
  <h2 class="card-title">Plusieurs variations de Lorem Ipsum peuvent</h2>
  <div class="news-date"><i></i>June 24, 2013</div>
  <p class="card-text">Le Lorem Ipsum est simplement du faux texte employé dans.</p>
</article>
<article class="card" style="left:642px;top:1585px;height:258px">
  <div class="card-photo" role="img" aria-label="Photo of students working together" style="background:linear-gradient(90deg,#2a2a2e,#c84a4a,#2f6fb0)"></div>
  <h2 class="card-title">Plusieurs variations de Lorem Ipsum peuvent</h2>
  <div class="news-date"><i></i>June 24, 2013</div>
  <p class="card-text">Le Lorem Ipsum est simplement du faux texte employé dans.</p>
</article>
<div class="view-all" style="top:1857px">View All</div>

<aside class="ad-slot ad-slot-top" role="img" aria-label="Advertisement banner slot"></aside>
<aside class="ad-slot ad-slot-mid" role="img" aria-label="Advertisement banner slot"></aside>
<aside class="ad-slot ad-slot-low" role="img" aria-label="Advertisement banner slot"></aside>

<footer class="site-footer abs">
  <div class="foot-col" style="left:20px"><h4>Company</h4><a>Contrairement</a><a>Opinion répandue</a><a>Pas simplement du</a><a>Texte aléatoire</a></div>
  <div class="foot-col" style="left:194px"><h4>Dictionnaire de</h4><a>Plusieurs variations</a><a>De Lorem Ipsum</a><a>Vent être</a></div>
  <div class="foot-col" style="left:377px"><h4>Trouvées ici ou</h4><a>Siècle est reproduit</a><a>Dessous pour les</a><a>CurieuxPlusieurs varia-</a><a>tions</a><a>De Lorem Ipsum</a></div>
  <div class="foot-col" style="left:554px"><h4>Embarassantes</h4><a>L'extrait standard</a><a>Utilisé depuis</a><a>Siècle est reproduit</a><a>Dessous pour les</a><a>Curieux</a><a>Vous voulez utiliser</a><a>Passage du Lorem</a></div>
  <div class="foot-col" style="left:718px"><h4>Stay updates on our Socail Network</h4>
    <div class="foot-social"><span></span><span></span><span></span></div>
    <h4>Join Our Newsletter</h4>
    <div class="newsletter"><div class="field">Enter your email address</div><div class="go">Subscribe</div></div>
  </div>
  <div class="copyright">© Copyrights 2013 All rights Reserved</div>
</footer>

</body>
</html>
```